Local Roofing/Construction company business needs new biz card design

We need a new business card design, current cards are from the start of this operation and generic at best. We are a local Construction Company (General Contractor) with a majority of our work originating from insurance claims-exterior finish work is the main focus (Roofs-Siding-Gutters etc). Heavily involved with homeowners and the low ball offers they receive from insurance company's after a insurable event takes place. I have attached some of our original logo file(s) below.

```html
<!DOCTYPE html>
<html lang="en">
<head>
<meta charset="utf-8">
<title>Northpeak Construction – Business Card</title>
<link rel="stylesheet" href="https://fonts.googleapis.com/css2?family=Montserrat:wght@800&family=Poppins:wght@400;700&display=swap">
<style>
  :root {
    --stage: #1d1d1d;
    --green: #34d97b;
    --ink: #0f1d1f;
    --paper: #ffffff;
    --text: #1a1a1a;
  }
  * { margin: 0; padding: 0; box-sizing: border-box; }
  html, body { width: 1200px; height: 1015px; overflow: hidden; }
  body {
    background: var(--stage);
    font-family: "Poppins", sans-serif;
    display: flex;
    flex-direction: column;
    align-items: center;
    justify-content: center;
    gap: 60px;
  }
  .card {
    position: relative;
    width: 640px;
    height: 366px;
    overflow: hidden;
  }
  .card-front {
    background: var(--green);
    display: flex;
    align-items: center;
    justify-content: center;
  }
  .brand {
    display: flex;
    align-items: center;
    gap: 16px;
    font-family: "Poppins", sans-serif;
    font-weight: 700;
    text-transform: uppercase;
    line-height: 1.05;
  }
  .brand-mark { width: 34px; height: 34px; flex: none; }
  .card-front .brand { color: var(--ink); font-size: 38px; }
  .card-front .brand-mark { background: var(--ink); }
  .brand-name small { display: block; font-size: 0.6em; letter-spacing: 0.14em; }

  .card-back { background: var(--paper); }
  .back-panel { position: absolute; inset: 0; }
  .back-brand {
    position: absolute;
    left: 430px;
    top: 42px;
    width: 170px;
    height: 282px;
    display: flex;
    align-items: center;
    justify-content: center;
  }
  .back-brand .brand { color: var(--paper); font-size: 24px; flex-direction: column; align-items: flex-start; gap: 10px; }
  .back-brand .brand-mark { background: var(--paper); }

  .contact {
    position: absolute;
    left: 48px;
    top: 88px;
    color: var(--text);
    font-size: 17px;
    line-height: 1.35;
  }
  .person-name {
    font-family: "Montserrat", sans-serif;
    font-weight: 800;
    color: var(--green);
    font-size: 24px;
    letter-spacing: 0.01em;
    line-height: 1.1;
  }
  .person-role { font-size: 17px; margin-bottom: 22px; }
  .contact-list { list-style: none; }
  .contact-list li { display: flex; align-items: center; gap: 10px; }
  .contact-list svg { width: 16px; height: 16px; flex: none; }
  .accent { color: var(--green); }
  .address { margin-top: 30px; }
</style>
</head>
<body>

  <section class="card card-front">
    <div class="brand">
      <span class="brand-mark"></span>
      <span class="brand-name">Northpeak<small>Construction</small></span>
    </div>
  </section>

  <section class="card card-back">
    <svg class="back-panel" viewBox="0 0 640 366" aria-hidden="true">
      <rect x="400" y="0" width="240" height="366" fill="var(--green)"/>
      <rect x="380" y="26" width="50" height="340" fill="var(--paper)"/>
      <rect x="380" y="330" width="150" height="36" fill="var(--paper)"/>
      <polygon points="416,26 590,26 614,50 614,316 590,340 416,340" fill="var(--paper)"/>
      <polygon points="446,42 584,42 600,58 600,308 584,324 446,324 430,308 430,58" fill="var(--green)"/>
    </svg>
    <div class="back-brand">
      <div class="brand">
        <span class="brand-mark"></span>
        <span class="brand-name">Northpeak<small>Construction</small></span>
      </div>
    </div>

    <div class="contact">
      <p class="person-name">MARCUS DELANEY</p>
      <p class="person-role">Managing Director</p>
      <ul class="contact-list">
        <li>
          <svg viewBox="0 0 16 16"><path d="M4 1.5l2.2 3-1.3 1.6a8 8 0 0 0 5 5l1.6-1.3 3 2.2-1.5 2.5C7.5 14.5 1.5 8.5 1.5 3z" fill="var(--green)"/></svg>
          044-555 018 274
        </li>
        <li>
          <svg viewBox="0 0 16 16"><rect x="1" y="3" width="14" height="10" fill="var(--green)"/><path d="M1 3l7 6 7-6" fill="none" stroke="var(--paper)" stroke-width="1.3"/></svg>
          hello@northpeak.com
        </li>
        <li>
          <svg viewBox="0 0 16 16"><circle cx="8" cy="8" r="6.5" fill="none" stroke="var(--green)" stroke-width="1.5"/><path d="M1.5 8h13M8 1.5c-3 3-3 10 0 13M8 1.5c3 3 3 10 0 13" fill="none" stroke="var(--green)" stroke-width="1.2"/></svg>
          <span>www.<span class="accent">northpeakbuild</span>.com</span>
        </li>
      </ul>
      <p class="address">88, Ridgeview Lane, Suite 4<br>40217, Cedar Falls</p>
    </div>
  </section>

</body>
</html>
```